Sale PPC Banner Ad Design Update

We need some Google PPC Banner Ad's for our sale altered to include product shots in the background. Attached are some examples that we currently use. We want a similar format/look but with the attached product shots used as the background image. Product image is called "KTPOle Grade 4"

Have also included our logo file as well.

Industry/Entity Type

Google

Font styles to use
Sans Serif

Requirements
Must have
• The must-have sizes (up to 150kb):
• • Banner: 468 x 60
• • Large mobile banner 320 x 100
• • Leaderboard: 728 x 90
• • Square: 250 x 250
• • Small square: 200 x 200
• • Large rectangle: 336 x 280
Nice to have
• The nice-to-have sizes:
• • Vertical rectangle: 240 x 400
• • Mobile leaderboard: 320 x 50
• • Inline rectangle: 300 x 250
• • Skyscraper: 120 x 600
• • Wide skyscraper: 160 x 600
• • Half-page: 300 x 600
• • Large leaderboard: 970 x 90
• • Billboard: 970 x 250
• • Portrait: 300 x 1050

```html
<!DOCTYPE html>
<html lang="en">
<head>
<meta charset="utf-8">
<title>KTPOle Grade 4 Sale Leaderboard</title>
<link rel="stylesheet" href="https://fonts.googleapis.com/css2?family=Cormorant+Garamond:wght@500&family=Montserrat:wght@500&family=Playfair+Display:wght@400&display=swap">
<style>
  :root {
    --paper: #ffffff;
    --ink: #151515;
    --gold: #d9c08a;
    --white: #f4f1ec;
    --rug-red: #7a1f1c;
    --rug-navy: #1e2440;
    --rug-dark: #141217;
    --rug-amber: #8a5a1c;
  }
  * { margin: 0; padding: 0; box-sizing: border-box; }
  html, body { width: 1200px; height: 148px; overflow: hidden; background: var(--paper); }
  .banner {
    position: relative;
    width: 1200px;
    height: 148px;
    display: flex;
  }
  .brand-strip {
    width: 49px;
    height: 148px;
    background: var(--paper);
    display: flex;
    align-items: center;
    justify-content: center;
    flex: none;
  }
  .brand-name {
    font-family: "Playfair Display", serif;
    font-weight: 400;
    font-size: 15px;
    color: var(--ink);
    white-space: nowrap;
    transform: rotate(-90deg);
  }
  .product-scene {
    position: relative;
    flex: 1;
    height: 148px;
    background:
      radial-gradient(ellipse at 50% 50%, rgba(10,8,12,0.75) 0%, rgba(10,8,12,0.35) 22%, rgba(10,8,12,0) 45%),
      linear-gradient(180deg, var(--rug-navy) 0%, var(--rug-navy) 14%, var(--rug-red) 30%, var(--rug-amber) 60%, var(--rug-red) 82%, var(--rug-dark) 100%);
  }
  .offer {
    position: absolute;
    left: 551px;
    top: 0;
    transform: translateX(-50%);
    text-align: center;
  }
  .offer-title {
    margin-top: 40px;
    font-family: "Cormorant Garamond", serif;
    font-weight: 500;
    font-size: 44px;
    line-height: 44px;
    letter-spacing: 7px;
    padding-left: 7px;
    color: var(--gold);
  }
  .offer-cta {
    margin-top: 12px;
    font-family: "Montserrat", sans-serif;
    font-weight: 500;
    font-size: 13px;
    letter-spacing: 2.5px;
    padding-left: 2.5px;
    color: var(--white);
  }
</style>
</head>
<body>
  <div class="banner">
    <div class="brand-strip">
      <span class="brand-name">KTPOle Grade 4</span>
    </div>
    <div class="product-scene" role="img" aria-label="Product shot: two-tone leather loafers worn with navy trousers, repeated across a colourful patterned rug">
      <div class="offer">
        <div class="offer-title">SALE</div>
        <div class="offer-cta">SHOP NOW</div>
      </div>
    </div>
  </div>
</body>
</html>
```